Advertising company unique advertising platform

we need a logo design for a new company based in Australia Melbourne. We develop innovated advertising platform where consumer can use this platform to get regular discount, as business owner they can use this platform for free advertisement. Payment for this advertisement platform only payable every two weeks, when I generate revenue for their business

Industry/Entity Type

Advertising

Contact Information for Business Card

Dale Morven | Co-Founder |Managing Director
Suite 718 240 Wattlebrook Lane Melbourne Vic 3000

ABN 38 614 207 923
Tel: +61 0487 259 318 | Email: dale.morven@plivorantu.com

Font styles to use
Decorative
Script

Requirements
Must have
• Try few different design and some round corner business card
Should not have
• One round corner business card...try 4 different colour background not only black, make sure two side is designed. Be creative so imagine you are giving this to a client make sure has wow factor, if you can also try one design with engrave like all the logo, words look 3d feel
• The word Advertising Platform use attached file font

```html
<!DOCTYPE html>
<html lang="en">
<head>
<meta charset="utf-8">
<title>Brightmarket business card</title>
<link rel="stylesheet" href="https://fonts.googleapis.com/css2?family=Roboto:wght@400;500;700&display=swap">
<style>
  :root {
    --backdrop: #e9e6e2;
    --flame-red: #e2452a;
    --flame-orange: #f08a35;
    --flame-yellow: #f6cf4e;
    --ink: #1f1a17;
    --charcoal: #262626;
    --teal: #3fe3c8;
    --teal-deep: #1aa6c9;
    --white: #ffffff;
    --accent: #f05a2b;
  }
  * { box-sizing: border-box; margin: 0; padding: 0; }
  html, body { width: 1200px; height: 886px; overflow: hidden; }
  body {
    background: var(--backdrop);
    font-family: "Roboto", Arial, sans-serif;
    position: relative;
  }
  .card {
    position: absolute;
    width: 540px;
    height: 330px;
    border-radius: 22px;
    overflow: hidden;
    box-shadow: 0 10px 28px rgba(0,0,0,0.22);
  }
  .card--front {
    left: 40px; top: 278px;
    background: radial-gradient(ellipse 70% 80% at 55% 42%, var(--flame-yellow) 0%, var(--flame-orange) 45%, var(--flame-red) 100%);
  }
  .card--back {
    left: 620px; top: 278px;
    background: radial-gradient(ellipse 60% 75% at 42% 40%, var(--flame-yellow) 0%, var(--flame-orange) 45%, var(--flame-red) 100%);
  }
  .front-brand {
    position: absolute;
    right: 46px; top: 126px;
    text-align: right;
  }
  .brand-name {
    font-weight: 700;
    font-size: 42px;
    letter-spacing: 0.5px;
    color: var(--ink);
    line-height: 1;
  }
  .front-web {
    margin-top: 10px;
    font-size: 13px;
    letter-spacing: 2.5px;
    color: var(--ink);
  }
  .back-shape { position: absolute; inset: 0; width: 100%; height: 100%; }
  .person {
    position: absolute;
    left: 62px; top: 30px;
    color: var(--ink);
  }
  .person-name { font-weight: 700; font-size: 17px; letter-spacing: 0.4px; }
  .person-role { font-size: 13px; line-height: 1.3; margin-top: 2px; }
  .back-brand {
    position: absolute;
    right: 40px; top: 118px;
    display: flex; align-items: center; gap: 10px;
  }
  .brand-dot {
    width: 30px; height: 30px; border-radius: 50%;
    background: var(--flame-orange);
  }
  .back-brand .brand-name { font-size: 30px; color: var(--flame-orange); }
  .contact {
    position: absolute;
    right: 40px; top: 190px;
    list-style: none;
    text-align: right;
    color: var(--white);
    font-size: 14.5px;
    line-height: 1.38;
  }
  .contact li { display: flex; justify-content: flex-end; align-items: center; gap: 7px; }
  .contact svg { width: 12px; height: 12px; fill: var(--accent); }
</style>
</head>
<body>
  <section class="card card--front" aria-label="Card front">
    <div class="front-brand">
      <div class="brand-name">Brightmarket</div>
      <div class="front-web">www.plivorantu.com</div>
    </div>
  </section>

  <section class="card card--back" aria-label="Card back">
    <svg class="back-shape" viewBox="0 0 540 330" preserveAspectRatio="none" aria-hidden="true">
      <defs>
        <linearGradient id="wave-teal" x1="0" y1="1" x2="1" y2="0">
          <stop offset="0" stop-color="#9fd6ff"/>
          <stop offset="0.5" stop-color="var(--teal-deep)"/>
          <stop offset="1" stop-color="var(--teal)"/>
        </linearGradient>
      </defs>
      <path d="M312 0 C240 18 222 130 150 200 C100 248 46 262 0 266 L0 282 C52 276 112 262 166 212 C236 146 262 26 330 0 Z" fill="url(#wave-teal)"/>
      <path d="M330 0 C262 26 236 146 166 212 C112 262 52 276 0 282 L0 330 L540 330 L540 0 Z" fill="var(--charcoal)"/>
    </svg>

    <div class="person">
      <div class="person-name">DALE MORVEN</div>
      <div class="person-role">Co-Founder<br>Managing Director</div>
    </div>

    <div class="back-brand">
      <span class="brand-dot"></span>
      <span class="brand-name">Brightmarket</span>
    </div>

    <ul class="contact">
      <li>Plivo Rantu</li>
      <li>ABN 38 614 207 923</li>
      <li>Suite 718 240 Wattlebrook Lane</li>
      <li>Melbourne Vic 3000</li>
      <li>+61 0487 259 318
        <svg viewBox="0 0 24 24" aria-hidden="true"><path d="M6.6 10.8a15.1 15.1 0 0 0 6.6 6.6l2.2-2.2c.3-.3.7-.4 1-.2 1.1.4 2.3.6 3.6.6.6 0 1 .4 1 1V20c0 .6-.4 1-1 1A17 17 0 0 1 3 4c0-.6.4-1 1-1h3.5c.6 0 1 .4 1 1 0 1.3.2 2.5.6 3.6.1.3 0 .7-.2 1z"/></svg>
      </li>
      <li>dale.morven@plivorantu.com
        <svg viewBox="0 0 24 24" aria-hidden="true"><path d="M2 5h20v14H2z M2 5l10 8 10-8" stroke="#262626" stroke-width="1.6"/></svg>
      </li>
    </ul>
  </section>
</body>
</html>
```